Business card for medical clinic

I need an upmarket, modern medical/health business card for my clinic

Contact Information for Business Card

name, address, email, qr code

```html
<!DOCTYPE html>
<html lang="en">
<head>
<meta charset="utf-8">
<title>Calder Health Partners – Business Card</title>
<link href="https://fonts.googleapis.com/css2?family=Montserrat:wght@400;700&display=swap" rel="stylesheet">
<style>
  :root {
    --backdrop: #cfd5d5;
    --card: #f1f1ef;
    --brand-blue: #1a72b4;
    --brand-navy: #123f6b;
    --ink: #3a3d40;
    --edge: #1f88c9;
  }
  * { box-sizing: border-box; margin: 0; padding: 0; }
  html, body { width: 1200px; height: 881px; overflow: hidden; }
  body {
    background: var(--backdrop);
    font-family: 'Montserrat', sans-serif;
    position: relative;
  }
  .card {
    position: absolute;
    top: 286px;
    width: 540px;
    height: 309px;
    background: var(--card);
    border-radius: 3px;
    box-shadow: 0 10px 24px rgba(0,0,0,0.12);
  }
  .card--front { left: 30px; border-bottom: 3px solid var(--edge); }
  .card--back { left: 630px; display: flex; align-items: center; justify-content: center; }

  .brand { display: flex; align-items: center; gap: 12px; }
  .brand__mark { flex: none; }
  .brand__name {
    font-weight: 700;
    color: var(--brand-blue);
    text-transform: uppercase;
    letter-spacing: 0.06em;
    line-height: 1.2;
  }
  .card--front .brand { position: absolute; left: 28px; top: 116px; width: 230px; }
  .card--front .brand__name { font-size: 17px; }
  .card--back .brand { gap: 18px; }
  .card--back .brand__name { font-size: 30px; }

  .divider {
    position: absolute;
    left: 276px; top: 56px;
    width: 1.5px; height: 200px;
    background: var(--brand-blue);
  }
  .contact { position: absolute; left: 300px; top: 58px; color: var(--ink); }
  .contact__name {
    font-weight: 700; font-size: 19px; color: var(--brand-blue);
    text-transform: uppercase; letter-spacing: 0.02em;
  }
  .contact__role { font-size: 13px; margin-top: 2px; }
  .contact__address { font-size: 13px; line-height: 1.45; margin-top: 16px; }
  .contact__list { list-style: none; margin-top: 18px; font-size: 13px; line-height: 1.75; }
  .contact__list li { display: flex; align-items: center; gap: 8px; }
  .contact__list svg { width: 12px; height: 12px; fill: var(--brand-navy); flex: none; }
</style>
</head>
<body>
  <section class="card card--front">
    <div class="brand">
      <svg class="brand__mark" width="44" height="44" viewBox="0 0 44 44" aria-hidden="true">
        <circle cx="22" cy="22" r="19" fill="none" stroke="var(--brand-blue)" stroke-width="3"/>
      </svg>
      <span class="brand__name">Calder Health Partners</span>
    </div>
    <div class="divider"></div>
    <div class="contact">
      <p class="contact__name">Daniel Moreau</p>
      <p class="contact__role">Managing Director</p>
      <p class="contact__address">Your address, City<br>State, Zip 1234</p>
      <ul class="contact__list">
        <li><svg viewBox="0 0 24 24" aria-hidden="true"><path d="M6.6 10.8a15 15 0 0 0 6.6 6.6l2.2-2.2c.3-.3.7-.4 1-.2 1.1.4 2.3.6 3.6.6.6 0 1 .4 1 1V20c0 .6-.4 1-1 1A17 17 0 0 1 3 4c0-.6.4-1 1-1h3.5c.6 0 1 .4 1 1 0 1.3.2 2.5.6 3.6.1.3 0 .7-.2 1z"/></svg>123 456 789</li>
        <li><svg viewBox="0 0 24 24" aria-hidden="true"><path d="M2 5h20v14H2zm2 2v.5l8 5 8-5V7zm0 2.9V17h16V9.9l-8 5z"/></svg>info@yourmail.com</li>
        <li><svg viewBox="0 0 24 24" aria-hidden="true"><path d="M12 2a10 10 0 1 0 0 20 10 10 0 0 0 0-20zm0 2c1 1.3 1.8 3.1 2 5h-4c.2-1.9 1-3.7 2-5zM4.3 13h3.7c.1 1.9.6 3.6 1.4 5A8 8 0 0 1 4.3 13zm0-2a8 8 0 0 1 5.1-5c-.8 1.4-1.3 3.1-1.4 5zM12 20c-1-1.3-1.8-3.1-2-5h4c-.2 1.9-1 3.7-2 5zm2.6-2c.8-1.4 1.3-3.1 1.4-5h3.7a8 8 0 0 1-5.1 5zM16 11c-.1-1.9-.6-3.6-1.4-5a8 8 0 0 1 5.1 5z"/></svg>www.yourwebsite.com</li>
      </ul>
    </div>
  </section>

  <section class="card card--back">
    <div class="brand">
      <svg class="brand__mark" width="70" height="70" viewBox="0 0 70 70" aria-hidden="true">
        <circle cx="35" cy="35" r="31" fill="none" stroke="var(--brand-blue)" stroke-width="4"/>
      </svg>
      <span class="brand__name">Calder Health<br>Partners</span>
    </div>
  </section>
</body>
</html>
```